Young, dynamic furniture company needs a new business card design

We require a new business card design for our modern furniture company which supplies furniture and appliances to the property and development market.
Oakridge Interiors has become one of the leading furniture & appliance suppliers to the property market withing London. With over 10 years experience, we have increased our business to supply not only private landlords and managing agents, but also property developers, housing associations and local councils.
We offer not only a complete range of furniture which includes beds, wardrobes, dining sets and sofas, but also a high quality, full delivery and assembly service to help you with all our furnishing needs.

Target Market(s)

Private landlords, estate agents, letting agents, property management companies

Industry/Entity Type

Business

Contact Information for Business Card

Name,
Title,
Address,
Mobile,
Telephone,
Fax, Website, email address

Font styles to use
Sans Serif

Colors
3176b5
0555a3
85abd2
cfdeed

Requirements
Must have
• All the above information for each of our staff, along with our logo

```html
<!DOCTYPE html>
<html lang="en">
<head>
<meta charset="utf-8">
<title>Oakridge Interiors – Business Card</title>
<link rel="stylesheet" href="https://fonts.googleapis.com/css2?family=Open+Sans:wght@400;600;700&family=Roboto:wght@300;400;700&display=swap">
<style>
  :root {
    --bg: #c9c8c6;
    --navy: #27306f;
    --navy-band: #1f3b78;
    --royal: #2b3a96;
    --bright: #1677c0;
    --sky: #85abd2;
    --ink: #1b1b1f;
    --white: #ffffff;
  }
  * { box-sizing: border-box; margin: 0; padding: 0; }
  html, body { width: 1200px; height: 994px; overflow: hidden; }
  body {
    background: var(--bg);
    position: relative;
    font-family: "Open Sans", Arial, sans-serif;
  }
  .card {
    position: absolute;
    width: 600px;
    height: 343px;
    overflow: hidden;
    box-shadow: 0 6px 18px rgba(0,0,0,.18);
  }

  /* ---------- Back side ---------- */
  .card-back { left: 80px; top: 80px; background: var(--navy); color: var(--white); }
  .card-back .brand {
    position: absolute; left: 0; right: 0; top: 112px;
    display: flex; flex-direction: column; align-items: center; gap: 8px;
  }
  .brand-row { display: flex; align-items: center; gap: 12px; }
  .brand-square { width: 26px; height: 26px; background: var(--bright); border: 2px solid var(--white); }
  .card-back .brand-name {
    font-family: "Roboto", Arial, sans-serif; font-weight: 300;
    font-size: 30px; letter-spacing: 1px; text-transform: uppercase;
  }
  .card-back .tagline {
    font-family: "Roboto", Arial, sans-serif; font-weight: 300;
    font-size: 13px; letter-spacing: 1.5px; text-transform: uppercase;
  }
  .card-back .site-line {
    position: absolute; left: 26px; right: 0; bottom: 26px;
    display: flex; align-items: center; gap: 10px;
  }
  .card-back .site { font-size: 15px; letter-spacing: .5px; }
  .card-back .rule { flex: 1; height: 1px; background: rgba(255,255,255,.8); }

  /* ---------- Front side ---------- */
  .card-front { left: 540px; top: 570px; background: var(--white); }
  .card-front svg.bands { position: absolute; inset: 0; }
  .holder {
    position: absolute; right: 22px; top: 44px;
    display: flex; align-items: center; gap: 10px;
  }
  .holder-text { text-align: right; line-height: 1; }
  .holder-name {
    font-family: "Open Sans", Arial, sans-serif; font-weight: 700;
    font-size: 20px; color: var(--ink); letter-spacing: .5px;
  }
  .holder-title {
    font-size: 12px; font-weight: 600; color: var(--navy); letter-spacing: 1px; margin-top: 3px;
  }
  .holder-icon {
    width: 30px; height: 30px; border-radius: 5px; background: var(--navy-band);
    display: flex; align-items: center; justify-content: center;
  }
  .card-front .brand {
    position: absolute; left: 90px; top: 120px;
    display: flex; flex-direction: column; gap: 6px;
  }
  .card-front .brand-name {
    font-family: "Roboto", Arial, sans-serif; font-weight: 400;
    font-size: 26px; color: var(--ink); text-transform: uppercase; letter-spacing: .5px;
  }
  .card-front .brand-square { border-color: var(--ink); }
  .card-front .tagline {
    font-family: "Roboto", Arial, sans-serif; font-weight: 300;
    font-size: 11.5px; color: #333; letter-spacing: 1.4px; text-transform: uppercase; padding-left: 38px;
  }
  .address {
    position: absolute; left: 26px; bottom: 10px;
    color: var(--white); font-size: 13px; line-height: 1.35;
  }
  .contacts {
    position: absolute; right: 18px; top: 182px;
    list-style: none; color: var(--white); text-align: right;
    font-size: 14px; font-weight: 600; line-height: 1;
  }
  .contacts li { display: flex; justify-content: flex-end; align-items: center; gap: 8px; margin-bottom: 7px; }
  .contacts svg { width: 17px; height: 17px; flex: none; }
</style>
</head>
<body>

  <section class="card card-back" aria-label="Business card, back">
    <div class="brand">
      <div class="brand-row">
        <span class="brand-square"></span>
        <span class="brand-name">Oakridge Interiors</span>
      </div>
      <span class="tagline">Trade Furniture Solutions</span>
    </div>
    <div class="site-line">
      <span class="site">www.website.com</span>
      <span class="rule"></span>
    </div>
  </section>

  <section class="card card-front" aria-label="Business card, front">
    <svg class="bands" width="600" height="343" viewBox="0 0 600 343">
      <!-- top header band -->
      <polygon points="0,0 600,0 600,8 312,8 298,34 0,34" fill="var(--navy-band)"/>
      <polygon points="316,16 600,16 600,23 313,23" fill="var(--bright)"/>
      <!-- contact panel -->
      <polygon points="350,160 600,160 600,343 336,343" fill="var(--navy-band)"/>
      <polygon points="338,206 344,206 330,343 324,343" fill="var(--bright)"/>
      <!-- address band -->
      <polygon points="0,264 336,208 324,343 0,343" fill="var(--white)"/>
      <polygon points="0,262 334,218 331,246 0,290" fill="var(--bright)"/>
      <polygon points="0,296 330,252 321,343 0,343" fill="var(--royal)"/>
    </svg>

    <div class="holder">
      <div class="holder-text">
        <div class="holder-name">YOUR NAME</div>
        <div class="holder-title">POSITION</div>
      </div>
      <div class="holder-icon">
        <svg width="18" height="18" viewBox="0 0 18 18"><circle cx="9" cy="5.5" r="3.5" fill="#fff"/><path d="M2 17c0-4 3-6.5 7-6.5s7 2.5 7 6.5z" fill="#fff"/></svg>
      </div>
    </div>

    <div class="brand">
      <div class="brand-row">
        <span class="brand-square"></span>
        <span class="brand-name">Oakridge Interiors</span>
      </div>
      <span class="tagline">Trade Furniture Solutions</span>
    </div>

    <p class="address">PO BOX 1234, Address Line 1,<br>Address Line 2,</p>

    <ul class="contacts">
      <li>123-456-7890
        <svg viewBox="0 0 18 18"><rect width="18" height="18" rx="3" fill="var(--sky)"/><path d="M5 4l2.5 0 1 3-1.5 1a7 7 0 0 0 3 3l1-1.5 3 1v2.5c-5 .5-9.5-4-9-9z" fill="#fff"/></svg></li>
      <li>123-456-7890
        <svg viewBox="0 0 18 18"><rect width="18" height="18" rx="3" fill="var(--sky)"/><rect x="5" y="3" width="8" height="4" fill="#fff"/><rect x="3" y="8" width="12" height="5" rx="1" fill="#fff"/><rect x="5" y="11" width="8" height="4" fill="#fff" stroke="var(--sky)"/></svg></li>
      <li>youremail@mailbox.com
        <svg viewBox="0 0 18 18"><rect width="18" height="18" rx="3" fill="var(--sky)"/><rect x="3" y="5" width="12" height="8" fill="#fff"/><path d="M3 5l6 5 6-5" fill="none" stroke="var(--sky)" stroke-width="1.2"/></svg></li>
      <li>www.website.com
        <svg viewBox="0 0 18 18"><rect width="18" height="18" rx="3" fill="var(--sky)"/><circle cx="9" cy="9" r="5.5" fill="none" stroke="#fff" stroke-width="1.3"/><ellipse cx="9" cy="9" rx="2.3" ry="5.5" fill="none" stroke="#fff" stroke-width="1"/><path d="M3.5 9h11" stroke="#fff" stroke-width="1"/></svg></li>
    </ul>
  </section>

</body>
</html>
```